A clean crisp business card for a Landscape Construction company. Designed to be easy to read contact/ info and also be appealing/interesting, unlike a traditional business card.

Industry/Entity Type

Landscape Construction

Contact Information for Business Card

Company name : Brambleford Landscape Construction, phone number: (877) 62Vista, website:Bramblefordyards.example, Email, sales@bramblefordyards.example

Requirements
Nice to have
• Luxurious finishes/ details…. Icons or emblems next to contact info
Should not have
• Clipart or general pictures

```html
<!DOCTYPE html>
<html lang="en">
<head>
<meta charset="utf-8">
<title>Brambleford Landscape Construction – Business Card</title>
<link href="https://fonts.googleapis.com/css2?family=Cinzel:wght@400;600&display=swap" rel="stylesheet">
<style>
  :root {
    --stage: #0d0d0e;
    --card: #141415;
    --lime: #a7d234;
    --blue: #1f6fd0;
    --emboss: #2a2a2c;
  }
  * { margin: 0; padding: 0; box-sizing: border-box; }
  html, body { width: 1200px; height: 820px; overflow: hidden; background: var(--stage); }
  .canvas { position: relative; width: 1200px; height: 820px; font-family: "Cinzel", serif; }
  .card {
    position: absolute; width: 540px; height: 310px;
    background: var(--card);
    border: 2px solid var(--lime);
    box-shadow: 0 18px 40px rgba(0,0,0,.7);
  }
  .card--front { left: 50px; top: 420px; }
  .card--back { left: 620px; top: 90px; }

  .holder { position: absolute; left: 34px; top: 40px; }
  .holder__name { color: var(--blue); font-size: 22px; font-weight: 600; letter-spacing: .5px; }
  .holder__title { color: var(--lime); font-size: 13px; letter-spacing: 1px; margin-top: 2px; }

  .brand { position: absolute; text-align: center; color: var(--blue); font-weight: 600; line-height: 1.1; }
  .card--front .brand { right: 30px; top: 40px; }
  .brand__name { font-size: 28px; letter-spacing: 1px; }
  .brand__line { font-size: 10.5px; letter-spacing: 3px; }
  .card--back .brand { right: 34px; top: 36px; }
  .card--back .brand__name { font-size: 32px; }

  .contact { position: absolute; left: 34px; top: 170px; list-style: none; }
  .contact__item { display: flex; align-items: center; gap: 8px; color: var(--lime); font-size: 12.5px; letter-spacing: .5px; height: 19px; }
  .contact__item--web { color: var(--blue); }
  .contact__icon { width: 13px; height: 13px; flex: none; fill: none; stroke: var(--blue); stroke-width: 1.6; }
  .address { position: absolute; left: 34px; top: 248px; color: var(--lime); font-size: 12.5px; letter-spacing: .5px; line-height: 1.4; }

  .back-seal { position: absolute; left: 150px; top: 130px; width: 150px; height: 150px; border-radius: 50%; background: var(--emboss); box-shadow: inset 2px 2px 4px rgba(255,255,255,.08), inset -3px -3px 6px rgba(0,0,0,.6); }
</style>
</head>
<body>
<main class="canvas">
  <section class="card card--front" aria-label="Business card front">
    <div class="holder">
      <p class="holder__name">Mara Ellison</p>
      <p class="holder__title">Managing Director</p>
    </div>
    <div class="brand">
      <p class="brand__name">Brambleford</p>
      <p class="brand__line">Landscape Construction</p>
    </div>
    <ul class="contact">
      <li class="contact__item">
        <svg class="contact__icon" viewBox="0 0 16 16"><path d="M3 2h3l1.5 3.5-2 1.2a8 8 0 0 0 3.8 3.8l1.2-2L14 10v3a1 1 0 0 1-1 1A11 11 0 0 1 2 3a1 1 0 0 1 1-1z"/></svg>
        (877) 62Vista
      </li>
      <li class="contact__item">
        <svg class="contact__icon" viewBox="0 0 16 16"><rect x="1.5" y="3.5" width="13" height="9"/><path d="M1.5 3.5 8 9l6.5-5.5"/></svg>
        sales@bramblefordyards.example
      </li>
      <li class="contact__item contact__item--web">
        <svg class="contact__icon" viewBox="0 0 16 16"><circle cx="8" cy="8" r="6.5"/><path d="M1.5 8h13M8 1.5c2.5 3 2.5 10 0 13M8 1.5c-2.5 3-2.5 10 0 13"/></svg>
        Bramblefordyards.example
      </li>
    </ul>
    <p class="address">421, Address Line Address<br>Goes Here 45452, Country Name</p>
  </section>

  <section class="card card--back" aria-label="Business card back">
    <div class="brand">
      <p class="brand__name">Brambleford</p>
      <p class="brand__line">Landscape Construction</p>
    </div>
    <div class="back-seal" aria-hidden="true"></div>
  </section>
</main>
</body>
</html>
```